Brand Identity Stationary Package

Hello I'm looking for a full branding package for my Property Management Company. I have a logo but looking to have the following
Business Card
Email signature
Facebook cover photo
Letterhead (word.doc)
#10 Envelope
Pocket Folder - link to 9x12 pocket folder design specs https://www.printorbit-example.ca/marketing-materials/presentation-folders
would like everything to match and be brand identifiable. The company looks after residential properties/apartments and some commercial properties. Attached is a zip of the files.
For Business Card
Name: Gareth Lindqvist
Position: Operations Manager
Number: 1 (555) 384-2917
Email: Gareth@harborkey-example.ca
Website: Harborkey-example.ca
Property Management

```html
<!DOCTYPE html>
<html lang="en">
<head>
<meta charset="utf-8">
<title>Harborkey Pocket Folder</title>
<link href="https://fonts.googleapis.com/css2?family=Montserrat:wght@400;500;600;700;800&display=swap" rel="stylesheet">
<style>
  :root {
    --backdrop: #b9b8b9;
    --green: #7fab3c;
    --green-dark: #6b9134;
    --ink: #1b1b1b;
    --paper: #f4f4f4;
    --paper-shade: #dcdcdc;
    --white: #ffffff;
  }
  * { box-sizing: border-box; margin: 0; padding: 0; }
  html, body { width: 982px; height: 1200px; overflow: hidden; }
  body {
    background: var(--backdrop);
    font-family: "Montserrat", sans-serif;
    color: var(--ink);
    position: relative;
  }
  .spread {
    position: absolute;
    left: 101px;
    width: 780px;
    height: 520px;
    display: flex;
    box-shadow: 0 18px 30px rgba(0,0,0,0.25);
  }
  .spread--outside { top: 30px; }
  .spread--inside { top: 640px; }
  .panel { position: relative; width: 390px; height: 520px; overflow: hidden; }

  /* Outside: back cover */
  .back-cover {
    background: linear-gradient(100deg, var(--green) 0%, var(--green-dark) 100%);
    color: var(--white);
  }
  .back-cover .wordmark {
    position: absolute; top: 70px; left: 0; width: 100%;
    text-align: center; font-size: 30px; font-weight: 800; letter-spacing: 2px;
    color: var(--white);
  }
  .back-cover .tagline {
    position: absolute; top: 418px; left: 0; width: 100%;
    text-align: center; font-size: 9px; font-weight: 700; line-height: 15px; letter-spacing: 0.3px;
  }
  .back-cover .divider {
    position: absolute; top: 458px; left: 40px; right: 40px; height: 1px;
    background: rgba(255,255,255,0.6);
  }
  .contact-row {
    position: absolute; top: 468px; left: 0; width: 100%;
    display: flex; justify-content: center; align-items: center; gap: 10px;
    font-size: 10px; font-weight: 400;
  }
  .contact-row span { display: flex; align-items: center; gap: 4px; }
  .contact-row svg { width: 9px; height: 9px; fill: currentColor; }

  /* Outside: front cover */
  .front-cover { background: linear-gradient(90deg, #e6e6e6 0%, var(--white) 40%); }
  .front-cover .wordmark {
    position: absolute; top: 58px; left: 0; width: 100%;
    text-align: center; font-size: 40px; font-weight: 800; letter-spacing: 2px;
  }
  .front-cover .wave { position: absolute; inset: 0; }

  /* Inside */
  .inside-left { background: linear-gradient(90deg, var(--white) 0%, #e4e4e4 60%, #bdbdbd 100%); }
  .inside-right { background: linear-gradient(90deg, #c8c8c8 0%, var(--paper) 25%, var(--white) 100%); }
  .pocket { position: absolute; inset: 0; }

  .letterhead {
    position: absolute; top: 22px; left: 28px; width: 334px; height: 480px;
    background: var(--white);
    box-shadow: -2px 3px 8px rgba(0,0,0,0.18);
    padding: 22px 20px;
    font-size: 5.6px; line-height: 7.4px;
  }
  .letterhead-header { display: flex; justify-content: space-between; align-items: flex-start; }
  .letterhead .wordmark { font-size: 17px; font-weight: 800; letter-spacing: 1px; margin-top: 22px; }
  .sender { font-size: 5.4px; line-height: 7.5px; }
  .sender-name { color: var(--green); font-weight: 700; }
  .sender-list { list-style: none; margin-top: 5px; }
  .sender-list li { display: flex; align-items: center; gap: 4px; }
  .sender-list svg { width: 5px; height: 5px; fill: var(--green); }
  .letterhead .rule { height: 1px; background: var(--green); margin: 14px 0 22px; }
  .recipient { margin-bottom: 6px; }
  .letter-body p { margin-bottom: 7px; text-align: justify; }
</style>
</head>
<body>

<section class="spread spread--outside">
  <div class="panel back-cover">
    <div class="wordmark">HARBORKEY</div>
    <p class="tagline">TENANTS, AND LANDLORDS<br>PROPERTY MANAGEMENT</p>
    <div class="divider"></div>
    <div class="contact-row">
      <span><svg viewBox="0 0 10 10"><path d="M2 1h2l1 2-1 1a5 5 0 0 0 2 2l1-1 2 1v2c0 1-1 1-1 1A8 8 0 0 1 1 2s0-1 1-1z"/></svg>1 (555) 384-2917</span>
      <span><svg viewBox="0 0 10 10"><path d="M0 2h10v6H0z M0 2l5 3 5-3" fill="none" stroke="currentColor" stroke-width="1"/></svg>Gareth@harborkey-example.ca</span>
      <span><svg viewBox="0 0 10 10"><circle cx="5" cy="5" r="4.5"/></svg>Harborkey-example.ca</span>
    </div>
  </div>
  <div class="panel front-cover">
    <div class="wordmark">HARBORKEY</div>
    <svg class="wave" viewBox="0 0 390 520" aria-hidden="true">
      <path d="M0 420 C110 470 200 488 280 440 C320 418 350 398 390 396 L390 520 L0 520 Z" fill="var(--green)"/>
      <path d="M0 408 C110 466 200 482 280 430 C320 404 350 386 390 384" fill="none" stroke="var(--ink)" stroke-width="6"/>
    </svg>
  </div>
</section>

<section class="spread spread--inside">
  <div class="panel inside-left">
    <svg class="pocket" viewBox="0 0 390 520" aria-hidden="true">
      <path d="M0 335 Q180 300 300 292 Q316 291 324 304 L390 520 L0 520 Z" fill="var(--green)"/>
    </svg>
  </div>
  <div class="panel inside-right">
    <article class="letterhead">
      <header class="letterhead-header">
        <div class="wordmark">HARBORKEY</div>
        <div class="sender">
          <div class="sender-name">GARETH LINDQVIST</div>
          <div>Operations Manager</div>
          <ul class="sender-list">
            <li><svg viewBox="0 0 10 10"><path d="M2 1h2l1 2-1 1a5 5 0 0 0 2 2l1-1 2 1v2c0 1-1 1-1 1A8 8 0 0 1 1 2s0-1 1-1z"/></svg>1 (555) 384-2917</li>
            <li><svg viewBox="0 0 10 10"><rect x="0" y="2" width="10" height="6"/></svg>Gareth@harborkey-example.ca</li>
            <li><svg viewBox="0 0 10 10"><circle cx="5" cy="5" r="4.5"/></svg>Harborkey-example.ca</li>
          </ul>
        </div>
      </header>
      <div class="rule"></div>
      <div class="recipient">Mr/s<br>First Name and Last Name<br>Company Name<br>Address</div>
      <div class="letter-body">
        <p>Lorem ipsum dolor sit amet, consectetur adipiscing sed do eiusmod tempor incididunt labore et dolore magna aliqua. Ut enim ad minim veniam, quis nostrud exercitation ullamco laboris nisi ut aliquip exea commodo consequat. Lorem ipsum dolor sit amet, consectetur adipiscing sed do eiusmod tempor incididunt labore et dolore magna aliqua. Ut enim</p>
        <p>Lorem ipsum dolor sit amet, consectetur adipiscing sed do eiusmod tempor incididunt labore et dolore magna aliqua. Ut enim ad minim veniam, quis nostrud exercitation ullamco laboris nisi ut aliquip exea commodo consequat. Duis aute irure dolor in reprehenderit in voluptate velit esse cillum irure dolor in reprehenderit in voluptate velit esse irure</p>
        <p>Lorem ipsum dolor sit amet, consectetur adipiscing sed do eiusmod tempor incididunt labore et dolore magna aliqua. Consequat. Duis aute irure dolor in reprehenderit in voluptate velit esse cillum dolore eu fugiat nulla pariatur. Excepteur sint occaecat cupidatat non proident, sunt in culpa qui officia deserunt mollit.</p>
        <p>Lorem ipsum dolor sit amet, consectetur adipiscing sed do eiusmod tempor incididunt labore et dolore magna aliqua. Ut enim Lorem ipsum dolor sit amet, consectetur adipiscing sed do eiusmod tempor incididunt labore et dolore magna aliqua. Ut enim Lorem ipsum aliqua ipsum</p>
        <p>Lorem ipsum dolor sit amet, consectetur adipiscing sed do eiusmod tempor incididunt labore et dolore magna aliqua. Ut enim ad minim veniam, quis nostrud exercitation ullamco laboris nisi ut aliquip exea commodo consequat. Duis aute irure dolor in reprehenderit in voluptate velit esse cillum irure dolor in reprehenderit in voluptate velit esse irure</p>
        <p>Lorem ipsum dolor sit amet, consectetur adipiscing sed do eiusmod tempor incididunt labore et dolore magna aliqua. Ut enim ad minim veniam, quis nostrud exercitation ullamco laboris nisi ut aliquip exea commodo.</p>
        <p>Regards,</p>
      </div>
    </article>
    <svg class="pocket" viewBox="0 0 390 520" aria-hidden="true">
      <path d="M0 520 L36 336 Q40 322 56 320 L390 292 L390 520 Z" fill="var(--green)"/>
    </svg>
  </div>
</section>

</body>
</html>
```